Heron Loan Partners Business Card

We need a business card design for our mortgage servicing company. In addition to servicing the loans of homeowners, we help homeowners with purchasing their homes and any mortgage refinancing. We would like to see designs that use the colors in the logo attached below (gold-ish yellow and navy blue), and any other design you deem fit! The design should communicate a simpler life with smart mortgages provided by Heron.

```html
<!DOCTYPE html>
<html lang="en">
<head>
<meta charset="UTF-8">
<title>Heron Loan Partners – Business Card</title>
<link rel="stylesheet" href="https://fonts.googleapis.com/css2?family=Libre+Baskerville:wght@700&family=Poppins:wght@400;500&display=swap">
<style>
  :root {
    --gold: #e3b23c;
    --gold-light: #ecc355;
    --gold-deep: #dca832;
    --navy: #1d1a4b;
    --white: #ffffff;
    --page: #e8e8e8;
  }
  * { margin: 0; padding: 0; box-sizing: border-box; }
  html, body { width: 1200px; height: 2400px; overflow: hidden; background: var(--page); }
  .sheet { position: relative; width: 1200px; height: 2400px; }

  .card {
    position: absolute; left: 100px; width: 1000px; height: 572px;
    overflow: hidden; background: var(--white);
    box-shadow: 0 6px 14px rgba(0,0,0,0.28);
  }
  .card--front { top: 588px; }
  .card--back { top: 1240px; }

  .card-texture {
    position: absolute; left: 0; top: 0; width: 100%;
    background: radial-gradient(ellipse at 30% 20%, var(--gold-light), transparent 60%),
                linear-gradient(135deg, var(--gold-light) 0%, var(--gold) 45%, var(--gold-deep) 100%);
  }
  .card--front .card-texture { height: 100%; }
  .card--back .card-texture { height: 285px; }

  .brand-name {
    position: absolute; font-family: 'Libre Baskerville', serif; font-weight: 700;
    color: var(--navy); white-space: nowrap; transform: translate(-50%, -50%);
  }
  .card--front .brand-name { left: 500px; top: 258px; font-size: 46px; }
  .card--back .brand-name { left: 770px; top: 132px; font-size: 27px; }

  .web-band { position: absolute; left: 0; width: 100%; height: 56px; }
  .card--front .web-band { top: 418px; }
  .card--back .web-band { top: 457px; }
  .web-band .bar { position: absolute; top: 16px; height: 24px; width: 160px; }
  .web-band .bar--left { left: 0; }
  .web-band .bar--right { right: 0; }
  .card--front .bar { background: var(--white); }
  .card--back .bar { background: var(--gold); }
  .web-address {
    position: absolute; left: 160px; right: 160px; top: 0; height: 56px;
    display: flex; align-items: center; justify-content: center;
    font-family: 'Libre Baskerville', serif; font-weight: 700;
    font-size: 40px; letter-spacing: 10px; color: var(--navy); white-space: nowrap;
  }

  .person { position: absolute; left: 73px; top: 70px; }
  .person-name {
    font-family: 'Libre Baskerville', serif; font-weight: 700;
    font-size: 46px; color: var(--navy); line-height: 1.1;
  }
  .person-title {
    margin-top: 8px; font-family: 'Poppins', sans-serif; font-weight: 500;
    font-size: 21px; letter-spacing: 6px; color: var(--white);
  }

  .contact { position: absolute; top: 246px; transform: translateX(-50%); text-align: center; }
  .contact--phone { left: 173px; }
  .contact--address { left: 468px; }
  .contact--email { left: 795px; }
  .contact-icon {
    display: block; margin: 0 auto; width: 78px; height: 78px;
  }
  .contact-text {
    margin-top: 22px; font-family: 'Poppins', sans-serif; font-weight: 400;
    font-size: 23px; line-height: 1.25; color: var(--navy); white-space: nowrap;
  }
  .contact--phone .contact-text { margin-top: 30px; }

  .divider {
    position: absolute; top: 300px; height: 130px; width: 0;
    border-left: 1.5px dashed var(--gold);
  }
  .divider--first { left: 310px; }
  .divider--second { left: 633px; }
</style>
</head>
<body>
<main class="sheet">

  <section class="card card--front" aria-label="Card front">
    <div class="card-texture" role="img" aria-label="Gold marbled texture background"></div>
    <div class="brand-name">Heron Loan Partners</div>
    <div class="web-band">
      <span class="bar bar--left"></span>
      <span class="web-address">www.heronloans.com</span>
      <span class="bar bar--right"></span>
    </div>
  </section>

  <section class="card card--back" aria-label="Card back">
    <div class="card-texture" role="img" aria-label="Gold marbled texture background"></div>

    <div class="person">
      <div class="person-name">Avery Lindqvist</div>
      <div class="person-title">FOUNDER &amp; CEO</div>
    </div>
    <div class="brand-name">Heron Loan Partners</div>

    <div class="contact contact--phone">
      <svg class="contact-icon" viewBox="0 0 78 78" aria-hidden="true">
        <circle cx="39" cy="39" r="37" fill="var(--gold)"/>
        <circle cx="39" cy="36" r="34" fill="var(--navy)"/>
        <path d="M28 25c2-2 4-2 5 0l3 5c1 2 0 3-1 4l-2 1c1 4 5 8 9 9l1-2c1-1 2-2 4-1l5 3c2 1 2 3 0 5l-2 2c-3 3-12-1-18-7s-10-15-7-18z" fill="var(--gold)"/>
        <path d="M42 22a12 12 0 0 1 12 12M42 27a7 7 0 0 1 7 7" stroke="var(--gold)" stroke-width="2.5" fill="none" stroke-linecap="round"/>
      </svg>
      <div class="contact-text">(555)-014-2290</div>
    </div>

    <div class="contact contact--address">
      <svg class="contact-icon" viewBox="0 0 78 78" aria-hidden="true">
        <circle cx="39" cy="39" r="37" fill="var(--gold)"/>
        <circle cx="39" cy="36" r="34" fill="var(--navy)"/>
        <path d="M39 18c-8 0-14 6-14 14 0 10 14 24 14 24s14-14 14-24c0-8-6-14-14-14z" fill="var(--gold)"/>
        <circle cx="39" cy="32" r="5.5" fill="var(--navy)"/>
      </svg>
      <div class="contact-text">418 Harbor Ave S,<br>Port Calder, FL 33900</div>
    </div>

    <div class="contact contact--email">
      <svg class="contact-icon" viewBox="0 0 78 78" aria-hidden="true">
        <circle cx="39" cy="39" r="37" fill="var(--gold)"/>
        <circle cx="39" cy="36" r="34" fill="var(--navy)"/>
        <rect x="24" y="26" width="30" height="21" fill="var(--gold)"/>
        <path d="M24 26l15 12 15-12M24 47l11-10M54 47l-11-10" stroke="var(--navy)" stroke-width="2" fill="none"/>
      </svg>
      <div class="contact-text">info@heronloans.com</div>
    </div>

    <span class="divider divider--first"></span>
    <span class="divider divider--second"></span>

    <div class="web-band">
      <span class="bar bar--left"></span>
      <span class="web-address">www.heronloans.com</span>
      <span class="bar bar--right"></span>
    </div>
  </section>

</main>
</body>
</html>
```